Hair salon Business Card

Beauty Salon
I would like to see designs using sky blue and a soft orange. Mainly I would like my name ( Gloss N' Wave Salon ) used as the design

Industry/Entity Type

Business

Contact Information for Business Card

Gloss N'Wave Salon
318 E Maple Hyw #14
Brookhaven, Ca 90000
555 555-2716

```html
<!DOCTYPE html>
<html lang="en">
<head>
<meta charset="utf-8">
<title>Gloss N' Wave Salon – Business Card</title>
<link href="https://fonts.googleapis.com/css2?family=Roboto:wght@400;700&display=swap" rel="stylesheet">
<style>
  :root {
    --backdrop: #d8d3cc;
    --card-blue: #189fe0;
    --pattern-blue: #3aaee6;
    --ink-white: #ffffff;
  }
  html, body {
    margin: 0;
    padding: 0;
    width: 1200px;
    height: 600px;
    overflow: hidden;
    background: var(--backdrop);
    font-family: "Roboto", Arial, sans-serif;
  }
  .canvas {
    position: relative;
    width: 1200px;
    height: 600px;
  }
  .card {
    position: absolute;
    left: 330px;
    top: 142px;
    width: 540px;
    height: 316px;
    background: var(--card-blue);
    overflow: hidden;
    color: var(--ink-white);
  }
  .card__pattern {
    position: absolute;
    inset: 0;
    background: radial-gradient(circle at 50% 50%, var(--card-blue) 0%, var(--pattern-blue) 140%);
  }
  .brand {
    position: absolute;
    left: 0;
    right: 0;
    top: 122px;
    text-align: center;
  }
  .brand__name {
    display: block;
    font-size: 44px;
    font-weight: 400;
    line-height: 1;
    letter-spacing: 1px;
    color: var(--ink-white);
  }
  .brand__rule {
    display: flex;
    align-items: center;
    justify-content: center;
    gap: 8px;
    margin: 9px auto 0;
    width: 358px;
  }
  .brand__rule::before,
  .brand__rule::after {
    content: "";
    flex: 1;
    height: 1px;
    background: var(--ink-white);
  }
  .brand__tag {
    font-size: 14px;
    font-weight: 700;
    letter-spacing: 0.5px;
    line-height: 1;
  }
  .contact {
    position: absolute;
    left: 0;
    right: 0;
    top: 282px;
    margin: 0;
    display: flex;
    justify-content: center;
    align-items: center;
    gap: 4px;
    font-size: 12.5px;
    line-height: 16px;
    white-space: nowrap;
  }
  .contact__icon {
    width: 11px;
    height: 11px;
    flex: none;
  }
  .contact__phone { margin-left: 3px; }
</style>
</head>
<body>
<main class="canvas">
  <section class="card">
    <div class="card__pattern" role="img" aria-label="Repeating pattern of small beauty and hair salon icons in light blue"></div>

    <div class="brand">
      <span class="brand__name">Gloss N' Wave</span>
      <div class="brand__rule"><span class="brand__tag">SALON</span></div>
    </div>

    <p class="contact">
      <svg class="contact__icon" viewBox="0 0 12 12" aria-hidden="true">
        <circle cx="6" cy="6" r="6" fill="#fff"/>
        <path d="M6 2.4a2.3 2.3 0 0 0-2.3 2.3C3.7 6.4 6 9.4 6 9.4s2.3-3 2.3-4.7A2.3 2.3 0 0 0 6 2.4z" fill="#189fe0"/>
        <circle cx="6" cy="4.7" r="0.9" fill="#fff"/>
      </svg>
      <span class="contact__address">318 E Maple Hyw #14,Brookhaven, Ca 90000</span>
      <svg class="contact__icon contact__phone" viewBox="0 0 12 12" aria-hidden="true">
        <circle cx="6" cy="6" r="6" fill="#fff"/>
        <rect x="4" y="2.5" width="4" height="7" rx="0.8" fill="#189fe0"/>
        <rect x="4.7" y="3.3" width="2.6" height="4.4" fill="#fff"/>
      </svg>
      <span class="contact__number">555 555-2716</span>
    </p>
  </section>
</main>
</body>
</html>
```